KOVA! Card

The single side "business card" will be utilized to write down product information for our customers. The card needs to include our logo in josefin font and read KOVA! on the front. Our brand colors are espresso brown and copper. The back needs to be white (blank) to allow us to write information down. We want modern, bold, clean and fun.
I have attached a copy of our logo but you do not have to utilize exactly as shown.

```html
<!DOCTYPE html>
<html lang="en">
<head>
<meta charset="utf-8">
<title>KOVA! Card</title>
<link rel="stylesheet" href="https://fonts.googleapis.com/css2?family=Josefin+Sans:wght@400&display=swap">
<style>
  :root {
    --espresso: #2a1911;
    --copper: #c2621f;
    --copper-text: #c86a28;
    --backdrop: #e4e2e6;
  }
  html, body {
    margin: 0;
    padding: 0;
    width: 1200px;
    height: 900px;
    overflow: hidden;
    background: var(--backdrop);
  }
  .canvas {
    position: relative;
    width: 1200px;
    height: 900px;
  }
  .card {
    position: absolute;
    left: 150px;
    top: 195px;
    width: 900px;
    height: 511px;
    background: var(--espresso);
    box-shadow: 0 6px 18px rgba(0, 0, 0, 0.25);
    font-family: "Josefin Sans", sans-serif;
    font-weight: 400;
  }
  .brand-band {
    position: absolute;
    left: 0;
    top: 82px;
    width: 545px;
    height: 292px;
    background: var(--copper);
    display: flex;
    align-items: center;
    padding-left: 80px;
    box-sizing: border-box;
  }
  .brand-name {
    font-size: 64px;
    color: var(--espresso);
    line-height: 1;
    padding-top: 8px;
  }
  .studio {
    position: absolute;
    left: 580px;
    top: 196px;
    width: 300px;
    color: var(--copper-text);
  }
  .studio-name {
    font-size: 40px;
    line-height: 1;
  }
  .studio-tagline {
    font-size: 22px;
    margin-top: 12px;
    line-height: 1.2;
  }
</style>
</head>
<body>
  <main class="canvas">
    <section class="card">
      <div class="brand-band">
        <span class="brand-name">KOVA!</span>
      </div>
      <div class="studio">
        <div class="studio-name">Halvors</div>
        <div class="studio-tagline">Jewelry &amp; Design Studio</div>
      </div>
    </section>
  </main>
</body>
</html>
```